Re-Design WP Site BrightHarbor.info

Site Re-design. Also Need a Button for contact on main page. Need Great Looking products re designed. Also bonus if you can install a site SEO checker on the site.

BrightHarbor.info

```html
<!DOCTYPE html>
<html lang="en">
<head>
<meta charset="utf-8">
<title>BrightHarbor.info – Social</title>
<link href="https://fonts.googleapis.com/css2?family=Montserrat:wght@400;500;600;700;800&display=swap" rel="stylesheet">
<style>
:root{
  --navy:#14195c;
  --navy-text:#1d2458;
  --blue:#1a8fe0;
  --cyan:#4fd0f2;
  --hero-a:#0a98e6;
  --hero-b:#5ee0f8;
  --grey:#7b7f8e;
  --pale:#f3f5fa;
  --pale-blue:#e3f1fc;
  --faint:#eceff4;
  --green:#22c36a;
  --white:#ffffff;
}
*{margin:0;padding:0;box-sizing:border-box}
html,body{width:1200px;height:2460px;overflow:hidden;background:var(--white)}
body{position:relative;font-family:'Montserrat',sans-serif;color:var(--navy-text)}
.abs{position:absolute}
.brand{display:flex;align-items:center;gap:8px;font-weight:500;font-size:19px;color:var(--navy);letter-spacing:.3px}
.brand-dot{width:14px;height:14px;border-radius:50%;background:var(--cyan)}
.nav{top:30px;left:587px;font-size:13px;font-weight:500;color:var(--navy-text)}
.nav span{position:absolute;white-space:nowrap}
.nav .active{color:var(--cyan)}
.hero{top:72px;left:0;width:1200px;height:550px;background:linear-gradient(100deg,var(--hero-a) 0%,#25b4ee 45%,var(--hero-b) 80%);overflow:hidden}
.hero-photo{position:absolute;left:530px;top:0;width:670px;height:550px;background:linear-gradient(90deg,rgba(244,214,170,.55),rgba(240,205,80,.5) 40%,rgba(70,90,140,.45) 70%,rgba(230,230,235,.6))}
.hero-title{left:124px;top:272px;font-size:45px;font-weight:800;color:var(--navy);line-height:1.1}
.hero-copy{left:127px;top:351px;width:400px;font-size:16.5px;line-height:20px;color:var(--white)}
.hero-kicker{left:127px;top:444px;font-size:13.5px;font-weight:700;color:var(--white)}
.btn{display:flex;align-items:center;justify-content:center;width:253px;height:44px;border-radius:22px;background:var(--navy);color:var(--white);font-size:13px;font-weight:700}
.section-title{left:284px;top:686px;font-size:22px;font-weight:600;color:var(--cyan)}
.perk{top:758px;height:100px;border-left:1px solid var(--faint);text-align:center;font-size:14px;font-weight:700;color:var(--navy)}
.perk svg{display:block;margin:10px auto 28px;height:42px}
.text{font-size:12.5px;line-height:20.7px;color:var(--grey)}
.acc{left:276px;width:647px;height:76px;border-radius:6px;background:var(--pale);display:flex;align-items:center;justify-content:space-between;padding:0 26px 0 44px;font-size:14px;font-weight:600;color:var(--navy)}
.acc.open{background:var(--pale-blue)}
.chev{width:30px;height:30px;border-radius:50%;background:var(--white);display:flex;align-items:center;justify-content:center}
.acc.open .chev{background:var(--blue)}
.checks{left:326px;top:1332px;list-style:none;font-size:12.5px;color:var(--grey)}
.checks li{display:flex;align-items:center;gap:12px;height:25.8px}
.step{top:1900px;width:260px}
.step-num{position:absolute;left:-38px;top:-20px;font-size:150px;font-weight:800;color:var(--faint);line-height:1}
.step h3{position:relative;font-size:21px;font-weight:600;color:var(--blue);margin-top:52px}
.step p{position:relative;font-size:13px;line-height:20px;color:var(--navy-text);margin-top:8px}
.footer{top:2142px;left:0;width:1200px;height:263px;background:var(--pale)}
.fcol{top:2198px;font-size:11px;color:var(--grey)}
.fcol h4{font-size:11px;font-weight:600;color:var(--navy-text);margin-bottom:22px}
.fcol a{display:block;color:var(--grey);text-decoration:none;line-height:20.7px}
.copyright{top:2432px;left:0;width:1200px;text-align:center;font-size:8px;color:#9aa0b4}
</style>
</head>
<body>

<header>
  <div class="abs brand" style="left:100px;top:33px"><span class="brand-dot"></span>BrightHarbor.info</div>
  <nav class="abs nav">
    <span style="left:0">Home</span>
    <span class="active" style="left:92px">Services ⌄</span>
    <span style="left:211px">Packages ⌄</span>
    <span style="left:333px">About</span>
    <span style="left:418px">Contact</span>
    <svg class="abs" style="left:506px;top:-3px" width="22" height="22" viewBox="0 0 24 24" fill="none" stroke="#14195c" stroke-width="2.4" stroke-linecap="round" stroke-linejoin="round"><path d="M3 12h12M11 7l5 5-5 5M15 3h5v18h-5"/></svg>
  </nav>
</header>

<section class="abs hero">
  <div class="hero-photo" role="img" aria-label="Three people holding large smiling emoji cards in front of their faces"></div>
</section>
<h1 class="abs hero-title">Social</h1>
<p class="abs hero-copy">We use sustainable methods to build your organic rankings, attract tons of natural links, and increase your local business traffic.</p>
<p class="abs hero-kicker">GET MORE INTERACTION...</p>
<div class="abs btn" style="left:127px;top:492px">Buy Now at $549</div>

<h2 class="abs section-title">WHAT YOU WILL GET:</h2>
<div class="abs perk" style="left:293px;width:121px">
  <svg viewBox="0 0 40 40"><path d="M20 2C10 2 2 9.5 2 19c0 5 2.3 9.5 6 12.6V38l6-3.3c1.9.5 3.9.8 6 .8 10 0 18-7.5 18-17S30 2 20 2z" fill="#14195c"/><circle cx="12" cy="19" r="2.5" fill="#fff"/><circle cx="20" cy="19" r="2.5" fill="#fff"/><circle cx="28" cy="19" r="2.5" fill="#fff"/></svg>Messages</div>
<div class="abs perk" style="left:414px;width:117px">
  <svg viewBox="0 0 30 40"><path d="M15 1C7.5 1 1.5 7 1.5 14.5 1.5 24 15 39 15 39s13.5-15 13.5-24.5C28.5 7 22.5 1 15 1z" fill="#14195c"/><circle cx="15" cy="14" r="5" fill="#fff"/></svg>Visits</div>
<div class="abs perk" style="left:531px;width:118px">
  <svg viewBox="0 0 48 40"><circle cx="17" cy="10" r="9" fill="#14195c"/><path d="M0 38c0-10 7.5-16 17-16s17 6 17 16z" fill="#14195c"/><path d="M42 12v12M36 18h12" stroke="#14195c" stroke-width="3.5"/></svg>Followers</div>
<div class="abs perk" style="left:649px;width:117px">
  <svg viewBox="0 0 40 40"><rect x="2" y="16" width="9" height="22" rx="2" fill="#14195c"/><path d="M14 18l8-14c3 0 5 2 4 6l-2 7h11c2.5 0 4 2 3.5 4.5l-3 13c-.5 2-2 3.5-4 3.5H14z" fill="#14195c"/></svg>Likes</div>
<div class="abs perk" style="left:766px;width:111px;border-right:1px solid var(--faint)">
  <svg viewBox="0 0 44 40"><path d="M22 39L4 21C-1 16 0 7 6 3.5 11 .5 17 2 22 7c5-5 11-6.5 16-3.5 6 3.5 7 12.5 2 17.5z" fill="#14195c"/></svg>Reputation</div>

<p class="abs text" style="left:279px;top:907px;width:640px">Lorem ipsum dolor sit amet, consectetur adipiscing elit. Quisque rutrum purus in ligula tincidunt, et dapibus ligula ornare. Nullam suscipit pretium lorem nec vulputate. Morbi felis purus, dapibus sit amet lacus eu, luctus feugiat lectus. Nulla facilisi. Morbi viverra tellus ullamcorper arcu consequat, at placerat nibh tempor. Proin suscipit dictum enim.</p>
<p class="abs text" style="left:279px;top:1010px;width:640px">Maecenas scelerisque neque in tellus consequat semper. Pellentesque molestie sapien vitae nunc facilisis tristique. Suspendisse sagittis magna vitae sodales auctor. Cras non facilisis lectus.</p>

<div class="abs acc open" style="top:1087px">SIMPLE<span class="chev"><svg width="12" height="8" viewBox="0 0 12 8" fill="none" stroke="#fff" stroke-width="2.2"><path d="M1 7l5-5 5 5"/></svg></span></div>
<p class="abs text" style="left:317px;top:1184px;width:578px">Lorem ipsum dolor sit amet, consectetur adipiscing elit. Quisque rutrum purus in ligula tincidunt, et dapibus ligula ornare. Nullam suscipit pretium lorem nec vulputate. Morbi felis purus, dapibus sit amet lacus eu, luctus feugiat lectus. Nulla facilisi. Morbi viverra tellus ullamcorper arcu consequat, at placerat nibh tempor. Proin suscipit dictum enim. Maecenas scelerisque neque in tellus consequat semper. Pellentesque molestie sapien vitae nunc facilisis tristique. Suspendisse sagittis magna vitae sodales auctor. Cras non facilisis lectus.</p>
<ul class="abs checks">
  <li><svg width="15" height="11" viewBox="0 0 15 11" fill="none" stroke="#22c36a" stroke-width="2.4"><path d="M1 5.5l4 4L14 1"/></svg>Donec porta sem id sodales gravida</li>
  <li><svg width="15" height="11" viewBox="0 0 15 11" fill="none" stroke="#22c36a" stroke-width="2.4"><path d="M1 5.5l4 4L14 1"/></svg>Morbi porttitor eros in neque</li>
  <li><svg width="15" height="11" viewBox="0 0 15 11" fill="none" stroke="#22c36a" stroke-width="2.4"><path d="M1 5.5l4 4L14 1"/></svg>Sed rhoncus vitae orci vel</li>
  <li><svg width="15" height="11" viewBox="0 0 15 11" fill="none" stroke="#22c36a" stroke-width="2.4"><path d="M1 5.5l4 4L14 1"/></svg>Quisque consequat pellentesque leo</li>
  <li><svg width="15" height="11" viewBox="0 0 15 11" fill="none" stroke="#22c36a" stroke-width="2.4"><path d="M1 5.5l4 4L14 1"/></svg>Suspendisse lacinia lorem lectus</li>
  <li><svg width="15" height="11" viewBox="0 0 15 11" fill="none" stroke="#22c36a" stroke-width="2.4"><path d="M1 5.5l4 4L14 1"/></svg>Curabitur eu finibus odio</li>
</ul>
<div class="abs btn" style="left:306px;top:1497px">Buy Now at $549</div>

<div class="abs acc" style="top:1600px">NORMAL<span class="chev"><svg width="12" height="8" viewBox="0 0 12 8" fill="none" stroke="#14195c" stroke-width="2.2"><path d="M1 1l5 5 5-5"/></svg></span></div>
<div class="abs acc" style="top:1691px">COMPLETE<span class="chev"><svg width="12" height="8" viewBox="0 0 12 8" fill="none" stroke="#14195c" stroke-width="2.2"><path d="M1 1l5 5 5-5"/></svg></span></div>

<div class="abs step" style="left:216px"><span class="step-num">1</span><h3>SEO Search Packages</h3><p>Outlived no dwelling denoting in peculiar as he believed.</p></div>
<div class="abs step" style="left:552px"><span class="step-num">2</span><h3>+ Power Boost</h3><p>Outlived no dwelling denoting in peculiar as he believed.</p></div>
<div class="abs step" style="left:888px"><span class="step-num">3</span><h3>Local Business</h3><p>Outlived no dwelling denoting in peculiar as he believed.</p></div>

<footer class="abs footer"></footer>
<div class="abs brand" style="left:97px;top:2256px"><span class="brand-dot"></span>BrightHarbor.info</div>
<div class="abs fcol" style="left:368px"><h4>Pages</h4><a>Home</a><a>Shop</a><a>Solutions</a><a>Blog</a><a>Contact</a><a>FAQ</a></div>
<div class="abs fcol" style="left:592px"><h4>Offers</h4><a>Page name</a><a>Page name</a><a>Page name</a><a>Page name</a><a>Page name</a><a>Page name</a></div>
<div class="abs fcol" style="left:805px"><h4>Downloads</h4><a>User Agreement</a><a>Privacy Policy</a><a>Refund Policy</a></div>
<p class="abs copyright">Copyright © 2022 BrightHarbor.info Use of this website constitutes acceptance of our User Agreement and Privacy Policy. Image by lumenstock.com</p>

</body>
</html>
```